Step and Repeat Backdrop for wedding reception photo booth

Would like to have a Step and Repeat Backdrop (8 foot high by 10 foot wide) that incorporates the wedding logo (attached) and the names Helen and Gavin. Background should be white, and wedding colors are burgundy and gold. Show me creativity :-) I have included some random samples.

```html
<!DOCTYPE html>
<html lang="en">
<head>
<meta charset="utf-8">
<title>Helen &amp; Gavin — Step and Repeat Backdrop</title>
<link rel="stylesheet" href="https://fonts.googleapis.com/css2?family=Playfair+Display:wght@600&display=swap">
<style>
  :root {
    --page: #eeeeee;
    --backdrop: #ffffff;
    --burgundy: #8a1419;
    --gold: #c4a032;
    --edge: rgba(0, 0, 0, 0.18);
  }
  html, body {
    margin: 0;
    width: 1200px;
    height: 600px;
    overflow: hidden;
    background: var(--page);
  }
  .canvas {
    position: relative;
    width: 1200px;
    height: 600px;
  }
  .backdrop {
    position: absolute;
    left: 225px;
    top: 0;
    width: 750px;
    height: 600px;
    background: var(--backdrop);
    box-shadow: 0 0 18px var(--edge);
    overflow: hidden;
  }
  .repeat-mark {
    position: absolute;
    width: 96px;
    margin-left: -48px;
    margin-top: -18px;
    text-align: center;
    font-family: "Playfair Display", Georgia, serif;
    font-weight: 600;
    font-size: 14px;
    line-height: 18px;
    color: var(--gold);
  }
  .feature-names {
    position: absolute;
    left: 175px;
    top: 150px;
    width: 400px;
    height: 300px;
    display: flex;
    flex-direction: column;
    align-items: center;
    justify-content: center;
    font-family: "Playfair Display", Georgia, serif;
    font-weight: 600;
    color: var(--burgundy);
    text-align: center;
  }
  .feature-names .rule {
    width: 260px;
    height: 2px;
    background: var(--burgundy);
  }
  .feature-names .names {
    margin: 22px 0;
    font-size: 62px;
    line-height: 70px;
  }
</style>
</head>
<body>
<main class="canvas">
  <section class="backdrop" aria-label="Step and repeat backdrop">
    <!-- outer columns -->
    <span class="repeat-mark" style="left:37px;top:113px">Helen<br>&amp; Gavin</span>
    <span class="repeat-mark" style="left:37px;top:238px">Helen<br>&amp; Gavin</span>
    <span class="repeat-mark" style="left:37px;top:365px">Helen<br>&amp; Gavin</span>
    <span class="repeat-mark" style="left:37px;top:490px">Helen<br>&amp; Gavin</span>

    <span class="repeat-mark" style="left:715px;top:113px">Helen<br>&amp; Gavin</span>
    <span class="repeat-mark" style="left:715px;top:238px">Helen<br>&amp; Gavin</span>
    <span class="repeat-mark" style="left:715px;top:365px">Helen<br>&amp; Gavin</span>
    <span class="repeat-mark" style="left:715px;top:490px">Helen<br>&amp; Gavin</span>

    <span class="repeat-mark" style="left:150px;top:47px">Helen<br>&amp; Gavin</span>
    <span class="repeat-mark" style="left:150px;top:175px">Helen<br>&amp; Gavin</span>
    <span class="repeat-mark" style="left:150px;top:302px">Helen<br>&amp; Gavin</span>
    <span class="repeat-mark" style="left:150px;top:430px">Helen<br>&amp; Gavin</span>
    <span class="repeat-mark" style="left:150px;top:557px">Helen<br>&amp; Gavin</span>

    <span class="repeat-mark" style="left:602px;top:47px">Helen<br>&amp; Gavin</span>
    <span class="repeat-mark" style="left:602px;top:175px">Helen<br>&amp; Gavin</span>
    <span class="repeat-mark" style="left:602px;top:302px">Helen<br>&amp; Gavin</span>
    <span class="repeat-mark" style="left:602px;top:430px">Helen<br>&amp; Gavin</span>
    <span class="repeat-mark" style="left:602px;top:557px">Helen<br>&amp; Gavin</span>

    <!-- inner columns around the feature -->
    <span class="repeat-mark" style="left:263px;top:113px">Helen<br>&amp; Gavin</span>
    <span class="repeat-mark" style="left:263px;top:490px">Helen<br>&amp; Gavin</span>
    <span class="repeat-mark" style="left:489px;top:113px">Helen<br>&amp; Gavin</span>
    <span class="repeat-mark" style="left:489px;top:490px">Helen<br>&amp; Gavin</span>
    <span class="repeat-mark" style="left:377px;top:47px">Helen<br>&amp; Gavin</span>
    <span class="repeat-mark" style="left:377px;top:557px">Helen<br>&amp; Gavin</span>

    <div class="feature-names">
      <span class="rule"></span>
      <h1 class="names" style="font-weight:600">Helen<br>&amp; Gavin</h1>
      <span class="rule"></span>
    </div>
  </section>
</main>
</body>
</html>
```